Steadfast hearts flyer

Benefits of prayer
- Prayer connects you to the God of fullness. Gal. 6:8
- Prayer places you cares on the Lord. 1 Peter 5:7, Matt. 11:28
- Prayer makes you fruitful in the vineyard of the Lord-this brings honour and glory. John 15:2
- Through prayer you exercise your Kingly authority. Matt. 16:19, 18:19.
- Prayer transforms you to be like Him. Luke 9:29.
- Prayer quickens divine inheritance. Luke 5:3-6
- Prayer will stir divine potentials in you. 2 Tim. 1:6
- And many more!

Experience the might and possibilities of prayer.

Join the Steadfast Hearts Ministry!

```html
<!DOCTYPE html>
<html lang="en">
<head>
<meta charset="utf-8">
<title>Steadfast Hearts Flyer</title>
<link rel="stylesheet" href="https://fonts.googleapis.com/css2?family=Allura&family=Fira+Sans+Condensed:ital,wght@1,600&family=Source+Sans+3:wght@400;600&display=swap">
<style>
  :root {
    --backdrop: #2a2a2a;
    --navy-deep: #141d3a;
    --navy: #1f3266;
    --sky: #3a6aa6;
    --white: #ffffff;
  }
  * { margin: 0; padding: 0; box-sizing: border-box; }
  html, body {
    width: 1200px; height: 1092px; overflow: hidden;
    background: var(--backdrop);
  }
  .flyer {
    position: absolute; left: 232px; top: 73px;
    width: 724px; height: 937px; overflow: hidden;
    background: linear-gradient(180deg, var(--navy-deep) 0%, var(--navy) 45%, var(--navy) 70%, var(--sky) 100%);
    font-family: "Source Sans 3", sans-serif;
    color: var(--white);
  }
  .flyer__photo {
    position: absolute; left: 330px; top: 0;
    width: 394px; height: 937px;
    background:
      radial-gradient(ellipse 200px 260px at 210px 220px, rgba(122,74,62,0.85), rgba(122,74,62,0) 70%),
      linear-gradient(90deg, rgba(42,59,110,0) 0%, rgba(42,59,110,0.6) 40%, rgba(20,29,58,0.7) 100%);
  }
  .brand {
    position: absolute; left: 46px; top: 90px;
    display: flex; align-items: center; gap: 16px;
  }
  .brand__mark {
    width: 48px; height: 48px; border-radius: 50%;
    background: var(--white);
  }
  .brand__name {
    font-family: "Source Sans 3", sans-serif; font-weight: 600;
    font-size: 26px; line-height: 1; color: var(--white);
    white-space: nowrap;
  }
  .headline {
    position: absolute; left: 48px; top: 243px;
    font-family: "Allura", cursive; font-weight: 400;
    font-size: 72px; line-height: 1; white-space: nowrap;
  }
  .benefits { position: absolute; left: 44px; top: 340px; list-style: none; width: 680px; }
  .benefits li {
    position: relative; padding-left: 26px;
    font-size: 20px; letter-spacing: 0.45px;
    line-height: 26px; margin-bottom: 25px;
    white-space: nowrap;
  }
  .benefits li::before {
    content: ""; position: absolute; left: 0; top: 6px;
    width: 15px; height: 15px; border-radius: 50%; background: var(--white);
  }
  .benefits li.benefits__more::before { display: none; }
  .tagline, .cta {
    position: absolute; left: 42px;
    font-family: "Fira Sans Condensed", sans-serif; font-style: italic; font-weight: 600;
    white-space: nowrap;
  }
  .tagline { top: 780px; font-size: 25px; }
  .cta { top: 827px; font-size: 36px; }
</style>
</head>
<body>
  <main class="flyer">
    <div class="flyer__photo" role="img" aria-label="Photo of a man in prayer holding a wooden cross against a cloudy blue sky"></div>

    <div class="brand">
      <span class="brand__mark"></span>
      <span class="brand__name">Northfield Chapel</span>
    </div>

    <h1 class="headline">Benefits of prayer</h1>

    <ul class="benefits">
      <li>Prayer connects you to the God of fullness. Gal. 6:8</li>
      <li>Prayer places you cares on the Lord. 1 Peter 5:7, Matt. 11:28</li>
      <li>Prayer makes you fruitful in the vineyard of the Lord-this<br>brings honour and glory. John 15:2</li>
      <li>Through prayer you exercise your Kingly authority. Matt. 16:19, 18:19.</li>
      <li>Prayer transforms you to be like Him. Luke 9:29.</li>
      <li>Prayer quickens divine inheritance. Luke 5:3-6</li>
      <li>Prayer will stir divine potentials in you. 2 Tim. 1:6</li>
      <li class="benefits__more">And many more!</li>
    </ul>

    <p class="tagline">Experience the might and possibilities of prayer.</p>
    <p class="cta">Join the Steadfast Hearts Ministry!</p>
  </main>
</body>
</html>
```